Corporate Travel Technology Company needs new Business Card design

We need a new business card design to reflect our re-branded company. Our company is called tolvEn (pronounced tolvenn) and we provide Business Intelligence and mobile travel management solutions for the corporate travel industry. Our multinational customers use our solutions to manage large travel budgets and frequent travellers, as well as to save money and reduce risk. We'd like to see designs that use the blue and green palette as well as our corporate logo (attached below). The design should communicate innovation, insight, forward thinking, contemporary, trusted.

Target Market(s)

Large multinational corporates and Travel Agencies.

Industry/Entity Type

Business

Contact Information for Business Card

Rosalind Mercer
Chief Executive
tolvEn
Phone number - +61 (0)2 8134 2907
Email address - rosalind.mercer@tolven-example.com
Mobile number - +61 (0)438 516 702
www.tolven-example.com

Font styles to use
Other font styles liked:
• Please use font as close to corporate logo as possible

Colors
0255a3
0393ce
00a990
33b8a4
33a6d7
3176b5

Requirements
Must have
• Please include the words;
• Mobile Travel Management
• Accelerating Travel Business Insights
• Use corporate logo - although icon can be stylised if needed

```html
<!DOCTYPE html>
<html lang="en">
<head>
<meta charset="utf-8">
<title>tolvEn business card</title>
<link rel="stylesheet" href="https://fonts.googleapis.com/css2?family=Arimo:wght@400;700&display=swap">
<style>
  :root {
    --bg: #e6e4e0;
    --ink-black: #0b0b0b;
    --card-white: #f7f7f7;
    --brand-blue: #0255a3;
    --brand-sky: #0393ce;
    --brand-teal: #00a990;
    --brand-aqua: #33b8a4;
    --brand-mid: #3176b5;
    --text-dark: #1d1d1d;
    --text-grey: #c9c9c9;
    --text-muted: #5f6f72;
  }
  * { margin: 0; padding: 0; box-sizing: border-box; }
  html, body { width: 1200px; height: 892px; overflow: hidden; }
  body {
    background: var(--bg);
    font-family: "Arimo", Arial, sans-serif;
    display: flex;
    align-items: center;
    justify-content: center;
    gap: 32px;
  }
  .card {
    position: relative;
    width: 560px;
    height: 342px;
    background: var(--card-white);
    box-shadow: 0 6px 18px rgba(0,0,0,0.18);
    overflow: hidden;
  }
  .card-front .wave { position: absolute; inset: 0; }
  .person { position: absolute; left: 34px; top: 140px; }
  .person-name { color: #fff; font-size: 27px; font-weight: 700; letter-spacing: 0.3px; }
  .person-title { color: var(--text-grey); font-size: 16px; margin-top: 8px; }
  .brand {
    display: flex;
    align-items: center;
    gap: 10px;
  }
  .brand-front { position: absolute; right: 34px; top: 28px; }
  .brand-mark {
    width: 26px; height: 26px;
    border-radius: 50%;
    border: 4px solid var(--brand-sky);
  }
  .brand-name { font-weight: 400; color: var(--brand-sky); line-height: 1; }
  .brand-front .brand-name { font-size: 42px; }
  .contact-list { position: absolute; list-style: none; }
  .contact-list li {
    display: flex; align-items: center; gap: 9px;
    font-size: 13px; color: var(--text-dark); height: 24px;
    white-space: nowrap;
  }
  .contact-phones { left: 40px; top: 286px; }
  .contact-online { left: 268px; top: 286px; }
  .icon {
    width: 14px; height: 14px; flex: none;
    background: var(--brand-aqua);
    border-radius: 2px;
    display: flex; align-items: center; justify-content: center;
  }
  .icon svg { width: 10px; height: 10px; }
  .card-back {
    display: flex; flex-direction: column;
    align-items: center; justify-content: center;
    gap: 22px;
  }
  .brand-back { gap: 16px; }
  .brand-back .brand-mark { width: 52px; height: 52px; border-width: 6px; }
  .brand-back .brand-name { font-size: 84px; }
  .taglines { text-align: center; }
  .tagline { font-size: 15px; color: var(--text-muted); letter-spacing: 1px; line-height: 1.6; }
  .tagline-primary { color: var(--brand-teal); font-weight: 700; }
</style>
</head>
<body>
  <section class="card card-front">
    <svg class="wave" viewBox="0 0 560 342" preserveAspectRatio="none" aria-hidden="true">
      <path d="M0 0 H560 V108 C490 110 442 148 384 202 C322 258 222 280 0 282 Z" fill="var(--brand-mid)"/>
      <path d="M0 0 H560 V100 C488 102 438 140 378 194 C316 250 218 270 0 272 Z" fill="var(--card-white)"/>
      <path d="M0 0 H560 V90 C486 92 434 130 372 184 C310 240 214 258 0 260 Z" fill="var(--ink-black)"/>
    </svg>

    <div class="person">
      <p class="person-name">Rosalind Mercer</p>
      <p class="person-title">Chief Executive</p>
    </div>

    <div class="brand brand-front">
      <span class="brand-mark"></span>
      <span class="brand-name">tolvEn</span>
    </div>

    <ul class="contact-list contact-phones">
      <li><span class="icon"><svg viewBox="0 0 10 10"><path d="M2 1 L4 1 L4.5 3 L3.5 4 C4 5.5 5 6.5 6 6.5 L7 5.5 L9 6 L9 8 C5 9 1 5 2 1 Z" fill="#fff"/></svg></span>+61 (0)2 8134 2907</li>
      <li><span class="icon"><svg viewBox="0 0 10 10"><rect x="3" y="1" width="4" height="8" rx="0.8" fill="none" stroke="#fff" stroke-width="1"/></svg></span>+61 (0)438 516 702</li>
    </ul>

    <ul class="contact-list contact-online">
      <li><span class="icon"><svg viewBox="0 0 10 10"><circle cx="5" cy="5" r="3.5" fill="none" stroke="#fff" stroke-width="1"/><path d="M1.5 5 H8.5 M5 1.5 V8.5" stroke="#fff" stroke-width="0.8"/></svg></span>www.tolven-example.com</li>
      <li><span class="icon"><svg viewBox="0 0 10 10"><rect x="1.5" y="2.5" width="7" height="5" fill="none" stroke="#fff" stroke-width="1"/><path d="M1.5 2.5 L5 5.5 L8.5 2.5" fill="none" stroke="#fff" stroke-width="1"/></svg></span>rosalind.mercer@tolven-example.com</li>
    </ul>
  </section>

  <section class="card card-back">
    <div class="brand brand-back">
      <span class="brand-mark"></span>
      <span class="brand-name">tolvEn</span>
    </div>
    <div class="taglines">
      <p class="tagline tagline-primary">Mobile Travel Management</p>
      <p class="tagline">Accelerating Travel Business Insights</p>
    </div>
  </section>
</body>
</html>
```